Harbor Ledger Funds Bus card and Logo

I need a logo design and Bus card design. The fund focuses on evaluating and investing in minerals (sub-surface rights) and real estate.

Harbor ledger refers to a book of knowledge that each plebe gets when entering the Kelmont Marine Academy (my alma mater)

Target Market(s)

Investors and financial advisors

Contact Information for Business Card

Simple - perhaps a logo with a theme on book of knowledge

Logo Text

Ex Scientia Imperium

Font styles to use
Serif
Sans Serif

Colors

Designer to choose colors to be used in the design.

Requirements
Must have
• memorable logo that is relatively simple

```html
<!DOCTYPE html>
<html lang="en">
<head>
<meta charset="utf-8">
<title>Harbor Ledger Funds – Business Card</title>
<link rel="stylesheet" href="https://fonts.googleapis.com/css2?family=Open+Sans:wght@400;600;700&display=swap">
<style>
  :root {
    --stage: #2e2e2e;
    --paper: #ffffff;
    --ink: #2b2b2b;
    --ink-soft: #444444;
    --rule: #9a9a9a;
    --green: #8cc63e;
    --blue: #3399cc;
    --teal: #4fae95;
  }
  * { box-sizing: border-box; margin: 0; padding: 0; }
  html, body {
    width: 1200px; height: 866px; overflow: hidden;
    background: var(--stage);
    font-family: "Open Sans", Arial, sans-serif;
  }
  .sheet {
    width: 1200px; height: 866px;
    display: flex; align-items: center; justify-content: center; gap: 50px;
  }
  .card {
    position: relative;
    width: 540px; height: 309px;
    overflow: hidden;
    box-shadow: 0 10px 24px rgba(0,0,0,.45);
  }

  /* Front */
  .card--front { background: var(--paper); color: var(--ink); }
  .card__band {
    position: absolute; left: 0; right: 0; bottom: 0; height: 9px;
    display: flex;
  }
  .card__band-green { width: 35%; background: var(--green); }
  .card__band-blue { flex: 1; background: var(--blue); }

  .contact { position: absolute; left: 30px; top: 38px; }
  .contact__name {
    color: var(--green); font-weight: 700; font-size: 17px;
    letter-spacing: .5px; text-transform: uppercase; line-height: 1.1;
  }
  .contact__role { font-size: 13px; color: var(--ink-soft); margin-bottom: 8px; }
  .contact__list { list-style: none; font-size: 13px; color: var(--ink-soft); line-height: 1.5; }
  .contact__list li { display: flex; align-items: center; gap: 7px; }
  .contact__list svg { width: 11px; height: 11px; fill: var(--green); flex: none; }

  .divider {
    position: absolute; left: 30px; top: 84px; width: 300px; height: 1px;
    background: var(--rule);
  }

  .brand { position: absolute; right: 34px; top: 120px; display: flex; align-items: center; gap: 12px; }
  .brand__dot { width: 38px; height: 38px; border-radius: 50%; background: var(--blue); flex: none; }
  .brand__name {
    font-weight: 700; font-size: 24px; line-height: 1.05;
    color: var(--ink); text-transform: uppercase; letter-spacing: 1px;
  }

  .address {
    position: absolute; right: 34px; bottom: 34px;
    font-size: 13px; color: var(--ink-soft); line-height: 1.4; text-align: right;
  }

  /* Back */
  .card--back {
    background: linear-gradient(160deg, var(--green) 0%, var(--teal) 50%, var(--blue) 100%);
    display: flex; align-items: center; justify-content: center;
  }
  .card--back .brand { position: static; }
  .card--back .brand__dot { background: var(--paper); width: 46px; height: 46px; }
  .card--back .brand__name { color: var(--paper); font-size: 30px; }
</style>
</head>
<body>
<main class="sheet">
  <section class="card card--front" aria-label="Business card front">
    <div class="contact">
      <p class="contact__name">Daniel Marsh</p>
      <p class="contact__role">Managing Director</p>
      <ul class="contact__list">
        <li><svg viewBox="0 0 12 12"><path d="M2 1h3l1 3-1.5 1a6 6 0 0 0 2.5 2.5L8 6l3 1v3a1 1 0 0 1-1 1A9 9 0 0 1 1 2a1 1 0 0 1 1-1z"/></svg>044-555 018 204</li>
        <li><svg viewBox="0 0 12 12"><path d="M3 0h6a1 1 0 0 1 1 1v10a1 1 0 0 1-1 1H3a1 1 0 0 1-1-1V1a1 1 0 0 1 1-1zm0 2v8h6V2z"/></svg>044-555 018 205</li>
        <li><svg viewBox="0 0 12 12"><path d="M0 2h12v8H0zm1 1v.5l5 3.5 5-3.5V3z"/></svg>info@harborledger.com</li>
        <li><svg viewBox="0 0 12 12"><circle cx="6" cy="6" r="5.5"/></svg>www.harborledgerfunds.com</li>
      </ul>
    </div>
    <div class="divider"></div>
    <div class="brand">
      <span class="brand__dot"></span>
      <p class="brand__name">Harbor Ledger<br>Funds</p>
    </div>
    <p class="address">12345, Address Goes Here<br>Country Name, 123456</p>
    <div class="card__band"><span class="card__band-green"></span><span class="card__band-blue"></span></div>
  </section>

  <section class="card card--back" aria-label="Business card back">
    <div class="brand">
      <span class="brand__dot"></span>
      <p class="brand__name">Harbor Ledger<br>Funds</p>
    </div>
  </section>
</main>
</body>
</html>
```